VOMRA Pty Ltd Business Card

Looking for a simple yet eye-catching double-sided business card design using my company logo on one side and contact details on the other.

Target Market(s)

Government

Industry/Entity Type

Communication Systems Engineering

Contact Information for Business Card

VOMRA Pty Ltd

Requirements
Nice to have
• Would be great to have a QR code so details can be scanned into contacts

```html
<!DOCTYPE html>
<html lang="en">
<head>
<meta charset="utf-8">
<title>VOMRA Pty Ltd Business Card</title>
<link href="https://fonts.googleapis.com/css2?family=Open+Sans:wght@400;600;700&display=swap" rel="stylesheet">
<style>
  :root {
    --stage: #222222;
    --card: #37424a;
    --card-deep: #2c353c;
    --ink-light: #ffffff;
    --ink-dark: #111111;
    --rule: #8a949b;
  }
  * { box-sizing: border-box; margin: 0; padding: 0; }
  html, body {
    width: 1200px; height: 780px; overflow: hidden;
    background: var(--stage);
    font-family: "Open Sans", Arial, sans-serif;
  }
  .stage {
    width: 1200px; height: 780px;
    display: flex; align-items: center; justify-content: center; gap: 40px;
  }
  .card {
    position: relative;
    width: 540px; height: 309px;
    background: var(--card);
    overflow: hidden;
  }
  /* front */
  .card-front {
    display: flex; align-items: center; justify-content: center;
  }
  .brand {
    display: flex; align-items: center; gap: 16px;
    font-weight: 700; letter-spacing: 4px;
  }
  .brand-dot {
    border-radius: 50%;
  }
  .card-front .brand { color: var(--card-deep); font-size: 64px; }
  .card-front .brand-dot { width: 70px; height: 70px; background: var(--card-deep); }
  /* back */
  .card-back .brand {
    position: absolute; top: 34px; left: 0; right: 0;
    justify-content: center;
    color: var(--ink-light); font-size: 46px;
  }
  .card-back .brand-dot { width: 52px; height: 52px; border: 2px solid var(--ink-light); }
  .person {
    position: absolute; left: 60px; top: 160px; width: 200px;
    text-align: right; color: var(--ink-light);
  }
  .person-name { font-size: 22px; font-weight: 700; line-height: 1.2; }
  .person-role { font-size: 14px; font-weight: 400; }
  .divider {
    position: absolute; left: 285px; top: 140px;
    width: 1px; height: 84px; background: var(--rule);
  }
  .contacts {
    position: absolute; left: 308px; top: 146px;
    list-style: none; color: var(--ink-light); font-size: 13px;
  }
  .contacts li { display: flex; align-items: center; gap: 8px; height: 24px; }
  .contacts svg { width: 13px; height: 13px; fill: var(--ink-light); flex: none; }
  .address-band {
    position: absolute; left: 0; right: 0; bottom: 22px; height: 28px;
    background: var(--ink-light); color: var(--ink-dark);
    display: flex; align-items: center; justify-content: center;
    font-size: 14px; font-weight: 400;
  }
</style>
</head>
<body>
<main class="stage">
  <section class="card card-front" aria-label="Card front">
    <div class="brand"><span class="brand-dot"></span><span>VOMRA</span></div>
  </section>

  <section class="card card-back" aria-label="Card back">
    <div class="brand"><span class="brand-dot"></span><span>VOMRA</span></div>

    <div class="person">
      <p class="person-name">Jordan Hale</p>
      <p class="person-role">Co-Founder</p>
    </div>

    <div class="divider"></div>

    <ul class="contacts">
      <li>
        <svg viewBox="0 0 24 24" aria-hidden="true"><path d="M6.6 10.8a15.1 15.1 0 0 0 6.6 6.6l2.2-2.2c.3-.3.7-.4 1-.2 1.1.4 2.3.6 3.6.6.6 0 1 .4 1 1V20c0 .6-.4 1-1 1A17 17 0 0 1 3 4c0-.6.4-1 1-1h3.5c.6 0 1 .4 1 1 0 1.3.2 2.5.6 3.6.1.3 0 .7-.2 1z"/></svg>
        <span>(555) 410-2286</span>
      </li>
      <li>
        <svg viewBox="0 0 24 24" aria-hidden="true"><path d="M12 2a10 10 0 1 0 0 20 10 10 0 0 0 0-20zm6.9 6h-3a15.6 15.6 0 0 0-1.4-3.6A8 8 0 0 1 18.9 8zM12 4c.8 1.2 1.5 2.5 1.9 4h-3.8c.4-1.5 1.1-2.8 1.9-4zM4.3 14a8 8 0 0 1 0-4h3.4a16.5 16.5 0 0 0 0 4zm.8 2h3a15.6 15.6 0 0 0 1.4 3.6A8 8 0 0 1 5.1 16zm3-8h-3a8 8 0 0 1 4.4-3.6C8.9 5.5 8.4 6.7 8.1 8zM12 20c-.8-1.2-1.5-2.5-1.9-4h3.8c-.4 1.5-1.1 2.8-1.9 4zm2.3-6H9.7a14.7 14.7 0 0 1 0-4h4.6a14.7 14.7 0 0 1 0 4zm.2 5.6c.6-1.1 1.1-2.3 1.4-3.6h3a8 8 0 0 1-4.4 3.6zm1.8-5.6a16.5 16.5 0 0 0 0-4h3.4a8 8 0 0 1 0 4z"/></svg>
        <span>www.vomra.com.au</span>
      </li>
      <li>
        <svg viewBox="0 0 24 24" aria-hidden="true"><path d="M2 5h20v14H2zm2 2v.5l8 5 8-5V7zm0 2.9V17h16V9.9l-8 5z"/></svg>
        <span>admin@vomra.com.au</span>
      </li>
    </ul>

    <p class="address-band">14-16 Harlow Lane Eastbrook NSW 2040 Australia</p>
  </section>
</main>
</body>
</html>
```